Brochure to attract insurance agents to outsource their bookkeeping

I need a brochure to handout at trade shows. Company name is Broker Office Ledger & Records. We go by BOLR. We provide bookkeeping services. I have attached the current brochure, which is a few years old, stale and outdated (not created on Pixmundo). I have also attached our graphic identity manual which show fonts/colors as well as our logo in 3 styles

Target Market(s)

Insurance Agents needing bookkeeping services

Industry/Entity Type

Accounting

Other font styles liked:
• See the graphic id manual

Colors
00AB8E
00BBA5
67D7C9
C6EFE9
E9F9F6

Requirements
Must have
• Services noted (see current brochure), contact info, reference to Vantrel Core

```html
<!DOCTYPE html>
<html lang="en">
<head>
<meta charset="utf-8">
<title>BOLR Brochure</title>
<link rel="stylesheet" href="https://fonts.googleapis.com/css2?family=Exo+2:wght@500;600;700&family=Barlow:wght@400;500;600&display=swap">
<style>
:root{
  --teal-deep:#00AB8E;
  --teal:#00BBA5;
  --teal-mid:#67D7C9;
  --teal-pale:#C6EFE9;
  --teal-mist:#E9F9F6;
  --stage:#ececec;
  --grey:#7b7b7b;
  --ink:#2b2b2b;
  --white:#ffffff;
  --head:"Exo 2",Arial,sans-serif;
  --body:"Barlow",Arial,sans-serif;
}
*{box-sizing:border-box;margin:0;padding:0}
html,body{width:970px;height:1200px;overflow:hidden}
body{background:var(--stage);font-family:var(--body);color:var(--ink);position:relative}
.panel{position:absolute;width:404px;height:514px;background:var(--white);overflow:hidden;box-shadow:0 1px 3px rgba(0,0,0,.12)}
.panel-about{left:78px;top:70px}
.panel-cover{left:498px;top:70px}
.panel-process{left:78px;top:601px}
.panel-why{left:498px;top:601px}
.abs{position:absolute}
.photo{position:absolute}

/* about panel */
.about-head{left:0;top:0;width:404px;height:218px;background:var(--teal-deep);color:var(--white)}
.about-title{left:22px;top:16px;width:370px;font-family:var(--head);font-weight:600;font-size:13.4px;line-height:16px;text-transform:uppercase}
.founder-photo{left:22px;top:85px;width:76px;height:106px;background:linear-gradient(160deg,#8a7a6a,#3c3a44)}
.founder-name{left:18px;top:196px;width:86px;text-align:center;font-family:var(--head);font-weight:600;font-size:7.5px;line-height:8px}
.founder-role{left:18px;top:205px;width:86px;text-align:center;font-size:7px}
.founder-bio{left:112px;top:85px;width:280px;font-size:7.6px;line-height:11.5px;text-align:justify}
.staff{top:236px;width:110px;text-align:center}
.staff-photo{width:64px;height:64px;margin:0 auto;border-radius:50%;border:3px solid var(--teal);background:linear-gradient(160deg,#c9b9a8,#6d6a70)}
.staff-name{margin-top:6px;font-family:var(--head);font-weight:600;font-size:8px;color:var(--teal-deep);text-transform:uppercase}
.staff-role{font-size:7.6px;line-height:9px}
.staff-strip{left:0;top:334px;width:404px;height:13px;background:var(--teal-deep);color:var(--white);font-size:7.2px;line-height:13px;padding-left:14px}
.about-foot{left:0;top:347px;width:404px;height:167px;background:linear-gradient(180deg,var(--teal-mist),#f7fcfb)}
.cta-box{left:14px;top:12px;width:146px;height:155px;background:var(--teal);color:var(--white);font-family:var(--head);font-weight:500;font-size:16.5px;line-height:22px;text-align:center;text-transform:uppercase;padding-top:26px}
.wordmark{font-family:var(--head);font-weight:700;color:var(--teal-deep);letter-spacing:.5px}
.foot-mark{left:196px;top:26px;font-size:30px;line-height:30px}
.foot-mark small{display:block;font-size:8.5px;line-height:10px;letter-spacing:0;font-weight:600;color:var(--grey)}
.contact{left:182px;top:82px;font-size:8.6px;line-height:12px}
.contact-row{display:flex;align-items:flex-start;gap:5px}
.contact svg{flex:none;margin-top:2px}
.social{left:196px;top:140px;display:flex;gap:5px}
.social span{width:15px;height:15px;border-radius:50%;background:var(--teal)}

/* cover panel */
.cover-photo{left:0;top:0;width:404px;height:196px;background:linear-gradient(120deg,#d9dedd 0%,#f2f3f1 45%,#c9ccc9 75%,#8d3b3b 100%)}
.cover-mark{left:14px;top:232px;width:118px}
.cover-mark .abbr{font-size:36px;line-height:36px}
.cover-mark small{display:block;font-size:7.4px;line-height:9px;color:var(--grey);font-weight:600;letter-spacing:0}
.cover-mark .full{font-size:12px;line-height:12.5px;letter-spacing:0}
.cover-head{left:131px;top:224px;width:273px;height:99px;background:var(--teal-deep);color:var(--white);padding:10px 10px 0 10px}
.cover-head h1{font-family:var(--head);font-weight:600;font-size:19px;line-height:21px;text-transform:uppercase}
.cover-head p{margin-top:6px;font-size:12px;line-height:14px}
.bar-services{left:0;top:323px;width:131px;height:22px;background:var(--teal-deep);color:var(--white);font-family:var(--head);font-size:10.5px;line-height:22px;text-align:center;font-weight:500}
.bar-web{left:131px;top:323px;width:273px;height:22px;background:var(--grey);color:var(--white);font-family:var(--head);font-size:11px;line-height:22px;padding-left:10px;font-weight:500}
.services{left:0;top:345px;width:404px;height:169px;background:linear-gradient(180deg,#f5fbfa,var(--teal-mist))}
.svc{width:90px;text-align:center;font-size:8px;line-height:10px;color:#4a4a4a}
.svc-icon{width:44px;height:44px;margin:0 auto 4px;border-radius:50%;background:var(--white);border:2px solid var(--teal-mid);display:flex;align-items:center;justify-content:center}

/* process panel */
.tab{left:60px;top:0;width:282px;height:28px;background:var(--teal);color:var(--white);font-family:var(--head);font-weight:500;font-size:12.5px;line-height:28px;text-align:center;text-transform:uppercase}
.intro{left:18px;top:50px;width:368px;font-size:8.4px;line-height:11.5px;text-align:justify}
.step{left:0;height:50px;display:flex;align-items:center;clip-path:polygon(0 0,calc(100% - 22px) 0,100% 50%,calc(100% - 22px) 100%,0 100%)}
.step.light{background:var(--teal-mist)}
.step.dark{background:var(--teal);color:var(--white)}
.step-num{width:40px;padding-left:8px;font-family:var(--head);font-size:27px;font-weight:500;color:var(--teal)}
.step.dark .step-num{color:var(--white)}
.step-text{font-size:8.2px;line-height:10.5px;padding-right:30px}
.process-photo{left:280px;top:354px;width:124px;height:160px;background:linear-gradient(180deg,#d9e9e6,#6b5a52 40%,#3a3d47)}

/* why panel */
.why-title{left:0;top:0;width:240px;height:50px;background:var(--white);color:var(--grey);font-family:var(--head);font-weight:500;font-size:13px;line-height:15px;padding:12px 0 0 38px;text-transform:uppercase}
.why-title::before{content:"";position:absolute;left:30px;top:10px;width:2px;height:32px;background:var(--teal-mid)}
.fees-title{left:240px;top:0;width:164px;height:50px;background:var(--grey);color:var(--white);font-family:var(--head);font-weight:500;font-size:13px;line-height:15px;padding:12px 0 0 12px;text-transform:uppercase}
.why-body{left:0;top:50px;width:240px;height:464px;background:var(--teal-deep);color:var(--white);padding:12px 10px 0 8px}
.reason{display:flex;gap:7px;margin-bottom:8px}
.reason svg{flex:none}
.reason h3{font-family:var(--head);font-weight:500;font-size:8.6px;line-height:10.5px;text-transform:uppercase;text-decoration:underline;margin-bottom:3px}
.reason p{font-size:7.3px;line-height:9.3px;text-align:justify}
.fees{left:240px;top:50px;width:164px;height:464px;background:var(--white)}
.calc-photo{left:0;top:0;width:164px;height:96px;background:linear-gradient(135deg,#f4f6f6,#cfd6d6 60%,#e8d7cc)}
.fees-text{left:14px;top:104px;width:142px;font-size:8px;line-height:10.5px}
.fee-table{left:14px;top:222px;width:142px;border-collapse:collapse;font-size:8px}
.fee-table th{background:var(--grey);color:var(--white);font-weight:500;text-align:left;font-size:7.2px;line-height:8.5px;padding:3px 4px}
.fee-table td{padding:1px 4px;line-height:11.5px}
.fee-table tr:nth-child(even) td{background:var(--teal-pale)}
.fees-note{left:14px;top:392px;width:142px;font-size:8px;line-height:10.5px}
.call-bar{left:10px;top:436px;width:154px;height:20px;background:var(--teal);color:var(--white);font-family:var(--head);font-weight:500;font-size:12.5px;line-height:20px;padding-left:6px}
.call-phone{left:14px;top:460px;font-family:var(--head);font-weight:600;font-size:17px;color:var(--teal-deep)}
</style>
</head>
<body>

<!-- About -->
<section class="panel panel-about">
  <div class="abs about-head">
    <h2 class="abs about-title">BOLR is a professional accounting/bookkeeping firm located in Connecticut dedicated exclusively to independent insurance agencies.</h2>
    <div class="photo founder-photo" role="img" aria-label="Portrait of the founder"></div>
    <div class="abs founder-name">MARLENE VOSBURGH</div>
    <div class="abs founder-role">Founder</div>
    <p class="abs founder-bio">BOLR's mission is to provide Independent Insurance Agencies a resource to have their accounting and bookkeeping performed accurately, timely and cost effectively. BOLR's 35 member staff is led by Marlene Vosburgh. Marlene worked in Independent Insurance Agencies for several years before forming BOLR in 2011. Her experience includes accounting, operational management, and client service. She earned a bachelor's degree in accounting from Eastfield State University and a master's degree in business administration from Northbrook University. Marlene is an adjunct accounting professor at Valley Community Colleges. She serves her community as President of the Harbor Civic Club.</p>
  </div>
  <div class="abs staff" style="left:22px"><div class="staff-photo" role="img" aria-label="Portrait of the director of accounting"></div><div class="staff-name">Owen Talcott</div><div class="staff-role">Director of Accounting</div></div>
  <div class="abs staff" style="left:148px"><div class="staff-photo" role="img" aria-label="Portrait of an accountant"></div><div class="staff-name">Priya Lindqvist</div><div class="staff-role">Accountant</div></div>
  <div class="abs staff" style="left:274px"><div class="staff-photo" role="img" aria-label="Portrait of an accountant"></div><div class="staff-name">Caleb Ostrander</div><div class="staff-role">Accountant</div></div>
  <div class="abs staff-strip">For a complete list of BOLR staff &amp; their profiles, please visit www.BrokerLedgerPros.com</div>
  <div class="abs about-foot">
    <div class="abs cta-box">Let BOLR be an integral part of your agency's success.</div>
    <div class="abs wordmark foot-mark"><small>Broker Office Ledger &amp; Records</small>BOLR</div>
    <div class="abs contact">
      <div class="contact-row"><svg width="8" height="9" viewBox="0 0 8 10"><path d="M4 0a3.5 3.5 0 0 0-3.5 3.5C.5 6 4 10 4 10s3.5-4 3.5-6.5A3.5 3.5 0 0 0 4 0zm0 5a1.4 1.4 0 1 1 0-2.8A1.4 1.4 0 0 1 4 5z" fill="#00AB8E"/></svg><span>47 Millstone Lane<br>Orchard Falls, CT 06000</span></div>
      <div class="contact-row"><svg width="8" height="8" viewBox="0 0 10 10"><path d="M2 0l2 2.5-1.2 1.3a6 6 0 0 0 3.4 3.4L7.5 6 10 8l-1.5 2C4 10 0 6 0 1.5z" fill="#00AB8E"/></svg><span>555.301.4827</span></div>
      <div class="contact-row"><svg width="8" height="8" viewBox="0 0 10 10"><circle cx="5" cy="5" r="4.3" fill="none" stroke="#00AB8E" stroke-width="1.2"/><path d="M.7 5h8.6M5 .7c-2.4 2.6-2.4 6 0 8.6M5 .7c2.4 2.6 2.4 6 0 8.6" fill="none" stroke="#00AB8E" stroke-width=".9"/></svg><span>www.BrokerLedgerPros.com</span></div>
    </div>
    <div class="abs social"><span></span><span></span><span></span></div>
  </div>
</section>

<!-- Cover -->
<section class="panel panel-cover">
  <div class="photo cover-photo" role="img" aria-label="Photo of a desk with a laptop showing profit charts and a person using a calculator"></div>
  <div class="abs wordmark cover-mark"><div class="abbr">BOLR</div><small>Broker Office</small><div class="full">LEDGER &amp; RECORDS</div></div>
  <div class="abs cover-head"><h1>Need help with Vantrel Core® accounting?</h1><p>The leading remote bookkeeping firm for Vantrel Core agencies nationwide</p></div>
  <div class="abs bar-services">SERVICES AVAILABLE</div>
  <div class="abs bar-web">BROKERLEDGERPROS.COM</div>
  <div class="abs services">
    <div class="abs svc" style="left:50px;top:8px"><div class="svc-icon"><svg width="22" height="22" viewBox="0 0 22 22"><rect x="2" y="5" width="18" height="12" rx="1.5" fill="none" stroke="#00AB8E" stroke-width="1.6"/><circle cx="11" cy="11" r="3" fill="none" stroke="#00AB8E" stroke-width="1.6"/></svg></div>Reconcile &amp; Pay Agency Bill Premiums</div>
    <div class="abs svc" style="left:157px;top:8px"><div class="svc-icon"><svg width="22" height="22" viewBox="0 0 22 22"><path d="M5 2h12v18l-2-1.5-2 1.5-2-1.5-2 1.5-2-1.5L5 20z" fill="none" stroke="#00AB8E" stroke-width="1.6"/><path d="M8 7h6M8 10h6M8 13h4" stroke="#00AB8E" stroke-width="1.4"/></svg></div>Record Direct Bill Commission</div>
    <div class="abs svc" style="left:264px;top:8px"><div class="svc-icon"><svg width="22" height="22" viewBox="0 0 22 22"><rect x="4" y="2" width="14" height="18" rx="1.5" fill="none" stroke="#00AB8E" stroke-width="1.6"/><path d="M7 7h8M7 10h8M7 13h5" stroke="#00AB8E" stroke-width="1.4"/></svg></div>Prepare &amp; Interpret Financial Statements</div>
    <div class="abs svc" style="left:6px;top:92px"><div class="svc-icon"><svg width="22" height="22" viewBox="0 0 22 22"><rect x="3" y="3" width="12" height="16" rx="1.5" fill="none" stroke="#00AB8E" stroke-width="1.6"/><rect x="12" y="10" width="7" height="9" rx="1" fill="#00AB8E"/><path d="M6 7h6M6 10h4" stroke="#00AB8E" stroke-width="1.4"/></svg></div>Reconcile General Ledger Accounts</div>
    <div class="abs svc" style="left:106px;top:92px"><div class="svc-icon"><svg width="22" height="22" viewBox="0 0 22 22"><circle cx="11" cy="8" r="5" fill="none" stroke="#00AB8E" stroke-width="1.6"/><path d="M2 17h6l3 2h5l4-3" fill="none" stroke="#00AB8E" stroke-width="1.6"/></svg></div>Reconcile Customer Accounts Receivable</div>
    <div class="abs svc" style="left:206px;top:92px"><div class="svc-icon"><svg width="22" height="22" viewBox="0 0 22 22"><rect x="2" y="5" width="18" height="12" rx="1.5" fill="none" stroke="#00AB8E" stroke-width="1.6"/><path d="M6 11h10M13 8l3 3-3 3" fill="none" stroke="#00AB8E" stroke-width="1.6"/></svg></div>Pay Vendor Invoices</div>
    <div class="abs svc" style="left:306px;top:92px"><div class="svc-icon"><svg width="22" height="22" viewBox="0 0 22 22"><rect x="3" y="4" width="16" height="15" rx="1.5" fill="none" stroke="#00AB8E" stroke-width="1.6"/><path d="M3 8h16M7 2v4M15 2v4" stroke="#00AB8E" stroke-width="1.6"/></svg></div>Process Payroll</div>
  </div>
</section>

<!-- Process -->
<section class="panel panel-process">
  <div class="abs tab">How outsourcing to BOLR works</div>
  <p class="abs intro">We access your Vantrel Core online database in the same manner as Agency staff. You provide the login credentials. Below is a high-level overview of the process. A detail operational workflow is provided to each client Agency.</p>
  <div class="abs step light" style="top:100px;width:252px"><span class="step-num">01</span><span class="step-text">Agency staff routes accounting documents to BOLR through Vantrel Core.</span></div>
  <div class="abs step dark" style="top:155px;width:305px"><span class="step-num">02</span><span class="step-text">Agency staff makes bank deposits of paper checks and cash, routing documentation to BOLR to record in Vantrel Core. BOLR records</span></div>
  <div class="abs step dark" style="top:208px;width:372px;background:var(--teal-deep)"><span class="step-num">03</span><span class="step-text">BOLR pays your vendors and insurance companies/brokers via Vantrel Core checks that you print, or via your bank's bill pay system, or via ACH. Agencies may choose the method.</span></div>
  <div class="abs step light" style="top:262px;width:350px"><span class="step-num">04</span><span class="step-text">BOLR reconciles Agency staff invoicing on all agency bill transactions with insurance company/broker records at time of payment. We work with your staff on discrepancies.</span></div>
  <div class="abs step dark" style="top:316px;width:330px;background:var(--teal-deep)"><span class="step-num">05</span><span class="step-text">BOLR records all direct bill commission at the time commission is received; this includes downloads, imports, and manual entry. You provide the commission statements or provide online access</span></div>
  <div class="abs step dark" style="top:369px;width:305px;background:var(--teal-mid)"><span class="step-num">06</span><span class="step-text">BOLR reconciles all bank accounts in Vantrel Core with your bank's data at least twice per week. You provide the login credentials.</span></div>
  <div class="abs step light" style="top:425px;width:280px"><span class="step-num">07</span><span class="step-text">BOLR sends financial statements to Agency Principals each month. We encourage review and discussion.</span></div>
  <div class="photo process-photo" role="img" aria-label="Photo of a smiling businesswoman with arms crossed"></div>
</section>

<!-- Why & fees -->
<section class="panel panel-why">
  <div class="abs why-title">Why outsourcing<br>to BOLR works</div>
  <div class="abs fees-title">How the BOLR fees<br>are structured</div>
  <div class="abs why-body">
    <div class="reason"><svg width="18" height="18" viewBox="0 0 18 18"><rect x="1" y="4" width="13" height="13" fill="none" stroke="#fff" stroke-width="1.5"/><path d="M4 10l3.5 3.5L17 2" fill="none" stroke="#fff" stroke-width="2.2"/></svg><div><h3>Our staff is educated in accounting &amp; trained in Vantrel Core</h3><p>The BOLR staff consists of Accountants, Bookkeepers, and Clerks. All are well trained in their responsibilities for Vantrel Core accounting. Accountants have earned bachelor's degrees in accounting and have several years of Vantrel Core experience; Bookkeepers have earned associate degree credits in accounting or have significant bookkeeping experience; Clerks have a variety of experiences and education levels, many are in school for accounting, all are detail oriented numbers people. Agency clients get the benefit of a full BOLR team.</p></div></div>
    <div class="reason"><svg width="18" height="18" viewBox="0 0 18 18"><rect x="1" y="4" width="13" height="13" fill="none" stroke="#fff" stroke-width="1.5"/><path d="M4 10l3.5 3.5L17 2" fill="none" stroke="#fff" stroke-width="2.2"/></svg><div><h3>Our work goes through a quality control process</h3><p>BOLR has a proprietary system of checks and balances to ensure client's financial statements are complete and accurate. All financial statement packages are prepared by our bookkeeping staff and reviewed by a staff accountant before presentation to the client. Agency principals are encouraged to discuss their statements with their BOLR accountant. Our goal is for our clients to understand their financial data, empowering them to make sound financial decisions.</p></div></div>
    <div class="reason"><svg width="18" height="18" viewBox="0 0 18 18"><rect x="1" y="4" width="13" height="13" fill="none" stroke="#fff" stroke-width="1.5"/><path d="M4 10l3.5 3.5L17 2" fill="none" stroke="#fff" stroke-width="2.2"/></svg><div><h3>We always have a backup</h3><p>When your BOLR Bookkeeper is out of the office a backup is always available. Should your BOLR Bookkeeper leave BOLR, another trained staff member will be available.</p></div></div>
    <div class="reason"><svg width="18" height="18" viewBox="0 0 18 18"><rect x="1" y="4" width="13" height="13" fill="none" stroke="#fff" stroke-width="1.5"/><path d="M4 10l3.5 3.5L17 2" fill="none" stroke="#fff" stroke-width="2.2"/></svg><div><h3>We implement controls for data security</h3><p>All computer equipment is owned by BOLR. PCs and routers are regularly updated to stay current with technology. All are continuously monitored for Orbix OS updates and virus/malware by an independent IT firm. Dual authentication is required for remote access to our PCs. Documents are shared within Vantrel Core or through a secure document sharing platform, Fileway Vault.</p></div></div>
  </div>
  <div class="abs fees">
    <div class="photo calc-photo" role="img" aria-label="Photo of a hand pressing keys on a calculator"></div>
    <p class="abs fees-text">Fees are a flat monthly rate based on annual policy commission revenue. The table below lists sample rates for our full-service offerings at different revenue volumes for an Agency with a typical mix of business and complexity. Fees assume compliance with our standard operating workflows.</p>
    <table class="abs fee-table">
      <thead><tr><th>Annual Commission Revenue</th><th>Monthly Service Fee</th></tr></thead>
      <tbody>
        <tr><td>&lt;$300,000</td><td>$600</td></tr>
        <tr><td>$700,000</td><td>$1,400</td></tr>
        <tr><td>$1,000,000</td><td>$2,000</td></tr>
        <tr><td>$1,500,000</td><td>$2,500</td></tr>
        <tr><td>$2,000,000</td><td>$3,000</td></tr>
        <tr><td>$2,500,000</td><td>$3,500</td></tr>
        <tr><td>$3,000,000</td><td>$4,500</td></tr>
      </tbody>
    </table>
    <p class="abs fees-note">We can provide services for larger agencies, typically supplementing in-house staff.</p>
    <div class="abs call-bar">CALL US TODAY</div>
    <div class="abs call-phone">555.301.4827</div>
  </div>
</section>

</body>
</html>
```